Identity Card Document Design

Looking for high quality identity card designs for templates.
Please read the detailed brief document which has sample designs and loads of info.
Instant Rejections :
1 You must NOT make anything illegal - anything which looks identical to an existing document. Create an ID card design entirely from scratch. Read the document for more info.
2 The artwork *has* to be provided as per the artwork specs in the document, as a print ready PDF to our size requirements.
3 No gen AI rubbish, don't waste your time, don't waste ours.
Question : In the document, there are certain letters which spell out a specific thing - what is this word? Please submit this word with your design.

```html
<!DOCTYPE html>
<html lang="en">
<head>
<meta charset="utf-8">
<title>Participant ID Card</title>
<link href="https://fonts.googleapis.com/css2?family=Arimo:wght@400;700&family=Roboto+Condensed:wght@400&display=swap" rel="stylesheet">
<style>
  :root {
    --page: #ffffff;
    --ink: #0d0d0d;
    --mint-light: #e4f3ea;
    --mint-mid: #d2eadc;
    --mint-deep: #bfe0cd;
    --photo-warm: #c9a68a;
    --photo-dark: #7a5a44;
    --badge: #3f6f5a;
  }
  * { margin: 0; padding: 0; box-sizing: border-box; }
  html, body {
    width: 872px; height: 1200px; overflow: hidden;
    background: var(--page);
  }
  body { position: relative; font-family: "Arimo", Arial, sans-serif; color: var(--ink); }

  .card {
    position: absolute; left: 32px; width: 806px; height: 531px;
    background: radial-gradient(ellipse at 50% 50%, var(--mint-light) 0%, var(--mint-mid) 60%, var(--mint-deep) 100%);
  }
  .card--front { top: 53px; }
  .card--back { top: 615px; }
  .card__frame {
    position: absolute; left: 13px; top: 12px; width: 781px; height: 506px;
    border: 1.6px solid var(--ink);
  }
  .card__guide {
    position: absolute; left: 22px; top: 21px; width: 763px; height: 488px;
    border: 1px dashed #8a9a90;
  }

  .abs { position: absolute; line-height: 1; white-space: nowrap; }
  .cond { font-family: "Roboto Condensed", "Arial Narrow", sans-serif; }

  .card-title { left: 71px; top: 83px; font-size: 40px; font-weight: 700; letter-spacing: 0.3px; }
  .card-type { left: 71px; top: 128px; font-size: 25px; display: flex; align-items: baseline; gap: 4px; }
  .card-type__number { font-size: 19px; font-weight: 700; }

  .expiry { right: 72px; top: 89px; font-size: 24px; display: flex; align-items: baseline; gap: 6px; }
  .expiry__value { font-family: "Arimo", Arial, sans-serif; font-weight: 700; font-size: 23px; }
  .country-badge {
    position: absolute; left: 552px; top: 123px; width: 42px; height: 27px;
    background: var(--badge); border-radius: 3px;
  }
  .country-code { left: 606px; top: 129px; font-size: 25px; }
  .prtc-code { right: 72px; top: 131px; font-size: 23px; font-weight: 700; }

  .field-label { left: 107px; font-size: 19px; }
  .field-value { left: 115px; font-size: 22.5px; }

  .photo {
    position: absolute;
    background: linear-gradient(180deg, var(--photo-dark) 0%, var(--photo-warm) 45%, #e3c2aa 100%);
  }
  .photo--small { left: 362px; top: 205px; width: 75px; height: 94px; opacity: 0.75; border-radius: 30px 30px 4px 4px; }
  .photo--main { left: 575px; top: 174px; width: 197px; height: 246px; border-radius: 90px 90px 12px 12px; }

  .holder-name { left: 553px; width: 240px; text-align: center; top: 428px; font-size: 23px; font-weight: 700; }
  .signature-label { left: 573px; width: 200px; text-align: center; top: 497px; font-size: 17px; }
  .signature-line { position: absolute; left: 573px; top: 523px; width: 200px; height: 2.4px; background: var(--ink); }
  .holder-number { left: 573px; width: 200px; text-align: center; top: 533px; font-size: 21px; font-weight: 700; letter-spacing: 3.5px; }

  .notice-title { left: 0; width: 872px; text-align: center; top: 813px; font-size: 32px; font-weight: 700; letter-spacing: 3px; }
  .notice-line { left: 87px; font-size: 20.5px; }
</style>
</head>
<body>

<section class="card card--front">
  <div class="card__frame"></div>
  <div class="card__guide"></div>
</section>

<div class="abs card-title">PARTICIPANT ID CARD</div>
<div class="abs card-type"><span>PARTICIPANT TYPE. No.</span><span class="card-type__number">10023456-222222</span></div>

<div class="abs expiry cond"><span>EXPIRY DATE :</span><span class="expiry__value">2025/2030</span></div>
<div class="country-badge" aria-hidden="true"></div>
<div class="abs country-code">CC</div>
<div class="abs prtc-code">PRTC 2000</div>

<div class="abs field-label cond" style="top:182px">FIRST NAME (S) :</div>
<div class="abs field-value" style="top:209px">MAREN HOLLOWAY</div>
<div class="abs field-label cond" style="top:236px">SURNAME :</div>
<div class="abs field-value" style="top:261px">MAREN</div>
<div class="abs field-label cond" style="top:288px">DATE OF BIRTH :</div>
<div class="abs field-value" style="top:314px">12-09-1997</div>
<div class="abs field-label cond" style="top:341px">PLACE OF STUDY :</div>
<div class="abs field-value" style="top:367px">PLACE OF STUDY</div>
<div class="abs field-label cond" style="top:396px">PLACE OF BIRTH :</div>
<div class="abs field-value" style="top:422px">PLACE OF BIRTH</div>
<div class="abs field-label cond" style="top:452px">ADDRESS :</div>
<div class="abs field-value" style="top:478px">ADDRESS 1, ADDRESS 2, ADDRESS 3</div>
<div class="abs field-value" style="top:504px">POSTCODE, COUNTRY</div>

<div class="photo photo--small" role="img" aria-label="Small ghost portrait photo of the card holder"></div>
<div class="abs field-label cond" style="left:362px; top:298px">GENDER :</div>
<div class="abs field-value" style="left:362px; top:321px">MALE / FAMALE</div>

<div class="photo photo--main" role="img" aria-label="Portrait photo of the card holder"></div>
<div class="abs holder-name">MAREN HOLLOWAY</div>
<div class="abs signature-label cond">(Signature)</div>
<div class="signature-line"></div>
<div class="abs holder-number">10023456</div>

<section class="card card--back">
  <div class="card__frame"></div>
  <div class="card__guide"></div>
</section>

<div class="abs notice-title">ATTENTION</div>
<div class="abs notice-line" style="top:913px">1. This card must be brought during the activity or as a participant</div>
<div class="abs notice-line" style="top:944px">2. This card cannot be transferred to another person even with permission</div>
<div class="abs notice-line" style="top:975px">from the card owner.</div>
<div class="abs notice-line" style="top:1006px">3. If you find this card, please return it to the owner of this card according to</div>
<div class="abs notice-line" style="top:1037px">the identity on the back of the card</div>
<div class="abs notice-line" style="top:1068px">4. This card is valid for as long as you are a participant</div>

</body>
</html>
```